Fernhale Business Card Design

We are looking for a fresh business card design for our new logo. We would like a business card that is unique but friendly. We are in the window coverings business offering blinds, shutters and shades for homes.

Target Market(s)

Targeting the end-consumer

Industry/Entity Type

Business

Requirements
Must have
• Must have a dedicates space for a photo of our sales person. Must contain our new logo (attached).

```html
<!DOCTYPE html>
<html lang="en">
<head>
<meta charset="utf-8">
<title>Fernhale Business Card</title>
<link rel="stylesheet" href="https://fonts.googleapis.com/css2?family=Cabin:wght@400;500&family=Roboto+Condensed:wght@400;700&display=swap">
<style>
  :root {
    --stage: #ecebe7;
    --card-white: #f7f7f5;
    --ink-grey: #6f6f6f;
    --rule-grey: #9a9a9a;
    --leaf-green: #8cc63f;
    --leaf-green-light: #9dd14c;
    --leaf-green-dark: #76b82a;
    --photo-tone: #f4f6ef;
  }
  * { box-sizing: border-box; margin: 0; padding: 0; }
  html, body { width: 1200px; height: 886px; overflow: hidden; }
  body { background: var(--stage); position: relative; font-family: "Roboto Condensed", sans-serif; }

  .card { position: absolute; box-shadow: 0 10px 30px rgba(0,0,0,.18); overflow: hidden; }

  /* Front */
  .card-front { left: 120px; top: 283px; width: 560px; height: 320px; background: var(--card-white); }
  .brand { position: absolute; display: flex; align-items: center; gap: 14px; white-space: nowrap; }
  .card-front .brand { left: 70px; top: 118px; color: var(--ink-grey); }
  .brand-square { width: 34px; height: 34px; border: 3px solid currentColor; border-radius: 4px; flex: none; }
  .brand-name { font-family: "Cabin", sans-serif; font-weight: 400; line-height: 1; }
  .card-front .brand-name { font-size: 52px; letter-spacing: .5px; }

  .divider { position: absolute; left: 110px; top: 206px; width: 410px; height: 1px; background: var(--rule-grey); }
  .divider-accent { position: absolute; left: 110px; top: 204px; width: 80px; height: 5px; background: var(--leaf-green); }

  .person { position: absolute; left: 110px; top: 218px; color: var(--ink-grey); font-size: 14px; line-height: 1.25; }
  .person-name { color: var(--leaf-green); font-weight: 700; font-size: 17px; letter-spacing: .3px; }

  .contact { position: absolute; right: 40px; top: 100px; text-align: right; color: var(--ink-grey); font-size: 14px; line-height: 1.3; }
  .contact-row { display: flex; align-items: center; justify-content: flex-end; gap: 8px; white-space: nowrap; }
  .contact-row svg { width: 11px; height: 11px; flex: none; }
  .contact-email { margin-top: 12px; }

  /* Back */
  .card-back { left: 760px; top: 163px; width: 320px; height: 560px;
    background: linear-gradient(160deg, var(--leaf-green-light), var(--leaf-green) 55%, var(--leaf-green-dark)); }
  .card-back .brand { left: 28px; top: 76px; color: #fff; gap: 12px; }
  .card-back .brand-square { width: 30px; height: 30px; }
  .card-back .brand-name { font-size: 38px; }
  .web { position: absolute; left: 30px; top: 126px; color: #fff; font-size: 11px; letter-spacing: 5px; white-space: nowrap; }
  .photo-area { position: absolute; left: 70px; top: 250px; width: 250px; height: 310px;
    border-radius: 110px 0 0 0; background: linear-gradient(180deg, #fff, var(--photo-tone)); }
</style>
</head>
<body>
  <section class="card card-front">
    <div class="brand">
      <span class="brand-square"></span>
      <span class="brand-name">Fernhale</span>
    </div>

    <div class="contact">
      <div class="contact-row">604 318 2795
        <svg viewBox="0 0 12 12"><path d="M3 1l2 2-1 1.5c.8 1.6 2 2.8 3.5 3.5L9 7l2 2-1.5 2C5 10.5 1.5 7 1 2.5z" fill="var(--leaf-green)"/></svg>
      </div>
      <div class="contact-row">604 318 4421
        <svg viewBox="0 0 12 12"><rect x="1" y="3" width="10" height="7" rx="1" fill="none" stroke="var(--leaf-green)" stroke-width="1.5"/></svg>
      </div>
      <div class="contact-row">604 318 9057
        <svg viewBox="0 0 12 12"><rect x="2" y="1" width="8" height="10" rx="1" fill="var(--leaf-green)"/></svg>
      </div>
      <div class="contact-row contact-email">hello@fernhale.com
        <svg viewBox="0 0 12 12"><rect x="1" y="1" width="10" height="10" rx="1" fill="var(--leaf-green)"/><path d="M3.5 6l2 2 3-4" fill="none" stroke="#fff" stroke-width="1.3"/></svg>
      </div>
    </div>

    <div class="divider"></div>
    <div class="divider-accent"></div>

    <div class="person">
      <div class="person-name">NORA ALDEN</div>
      <div>CEO/FOUNDER</div>
      <div>214 Larkspur Row</div>
      <div>Halden, Oregon 97120</div>
    </div>
  </section>

  <section class="card card-back">
    <div class="brand">
      <span class="brand-square"></span>
      <span class="brand-name">Fernhale</span>
    </div>
    <div class="web">www.fernhale.com</div>
    <div class="photo-area" role="img" aria-label="Photo of the sales person"></div>
  </section>
</body>
</html>
```